The Velvet Easel Co - Photos to Custom Oil Paintings

We need a website and logo designed and built allowing customers to purchase custom oil paintings. The paintings will come from a customers single photograph or even combination of photos. They will be able to complete a straight forward checkout process, selecting their desired medium (oil or charcoal painting), their desired size, the number of figures in the painting, the type of background required (as per photo or let the artist decide). Which will then automaticaly provide the customer with a price for the purchase. Allowing them to add a photo to the order which they can then submit with the order present in their personal account etc etc etc.
Theres one website in particular that i will be competing with. That is based in the US - http://www.brushmorrow.com
I wish to far exceed the appearence of the already present site.
At the moment i wish to include Coinvale in the payment process. Unless there are some cheaper, more cost efficient ways, please let me know.
The company name is The Velvet Easel Co. Domain has been purchased - www.thevelveteasel.co (via Hostlark - Linux)
I have no great sense of design, but the site must be straight forward, eye catching, engaging and give the customer a sense of high quality. Some kind of flash animation with pictures on the front page scrolling?
For myself, the admin side, ideally must be straight forward to maintain. The ability to update customers accounts with info (they will then be informed there is an update in their account etc)
The ability for automated emails from point of sale (sales orders with generated order numbers) to myself. Again automated emails to the customers once the "status" of their order or other information has been submitted to their account (by myself) or a similar system.
Updates
All,
Please note, the budget is able to increase subject to what additional work is needed. As far as the admin area goes. I am open to suggestions to ensure ease of use and efficiency.
Any questions, comments or ideas are fully welcomed.
Many thanks,
Dan Holloway
Industry/Entity Type
It Company
Logo Text
Logo styles of interest
Pictorial/Combination Logo
Abstract Logo
Wordmark Logo
Lettermark Logo
Look and feel
Each slider illustrates characteristics of the customer's brand and the style your logo design should communicate.

```html
<!DOCTYPE html>
<html lang="en">
<head>
<meta charset="utf-8">
<title>The Velvet Easel — Custom Oil Paintings</title>
<link rel="stylesheet" href="https://fonts.googleapis.com/css2?family=Arimo:wght@400;700&family=Lato:wght@300;400&display=swap">
<style>
:root{
  --page-bg:#0a0a0a;
  --panel:#ffffff;
  --ink:#333333;
  --ink-soft:#444444;
  --accent-red:#b3141d;
  --orange:#f7a21b;
  --orange-deep:#e8870c;
  --login-top:#f2981c;
  --login-bottom:#c0281c;
  --button-dark:#111111;
  --search-panel:#4c4c4c;
  --rule:#d8d8d8;
}
*{box-sizing:border-box;margin:0;padding:0}
html,body{width:800px;height:1200px;overflow:hidden}
body{
  position:relative;
  background:radial-gradient(ellipse at 50% 10%,#1c1c1c 0%,var(--page-bg) 60%);
  font-family:"Arimo",Arial,sans-serif;
  color:var(--ink);
}
.abs{position:absolute}

/* header */
.brand{left:36px;top:48px;display:flex;align-items:center;gap:14px}
.brand-dot{width:40px;height:40px;border-radius:50%;background:var(--orange)}
.brand-name{font-family:"Lato",sans-serif;font-weight:300;font-size:36px;color:#fff;letter-spacing:.5px}
.search{left:525px;top:36px;width:230px;height:69px;background:var(--search-panel);border-radius:4px;opacity:.92}
.search-field{left:16px;top:28px;width:134px;height:18px;background:#fff;border:1px solid #ccc}
.search-btn{left:159px;top:27px;width:61px;height:19px;border-radius:3px;background:linear-gradient(#ffb640,var(--orange-deep));color:#fff;font-size:11px;font-weight:700;text-align:center;line-height:19px}

/* main panel */
.panel{left:36px;top:138px;width:715px;height:987px;background:var(--panel);border-radius:6px}
.nav{left:0;top:0;width:715px;height:46px;display:flex;font-size:11px;color:var(--ink);background:linear-gradient(#fff,#f2f2f2)}
.nav a{position:absolute;top:17px;color:inherit;text-decoration:none;white-space:nowrap}

.hero{left:2px;top:46px;width:711px;height:334px;background:linear-gradient(90deg,#8a1010 0%,#c9c9c9 25%,#eeeeee 45%,#9b9b9b 60%,#d8d8d8 75%,#8c0c0c 100%)}
.hero-bar{left:0;bottom:0;width:100%;height:30px;background:rgba(40,40,40,.75)}
.hero-caption{left:46px;top:256px;width:400px;color:#fff;font-size:14.5px;line-height:24px}
.dots{right:14px;bottom:6px;display:flex;gap:3px}
.dots span{width:14px;height:14px;border-radius:50%;background:#fff}
.dots span:first-child{background:var(--orange)}

/* sidebar */
.login{left:12px;top:397px;width:190px;height:153px;border-radius:4px;background:linear-gradient(var(--login-top),var(--login-bottom))}
.login-head{left:7px;top:8px;width:178px;height:27px;border-radius:5px;background:linear-gradient(#fff,#e6e6e6);font-size:13px;color:#222;line-height:27px;padding-left:33px}
.login-head svg{position:absolute;left:12px;top:7px}
.field-label{left:8px;color:#fff;font-size:10.5px}
.field-input{left:70px;width:112px;height:21px;background:#fff;border:1px solid #b33}
.btn-dark{background:linear-gradient(#3a3a3a,var(--button-dark));color:#fff;font-size:10.5px;text-align:center;border-radius:3px}
.submit{left:103px;top:112px;width:65px;height:25px;line-height:25px}

.upload{left:12px;top:565px;width:190px;height:199px;background:linear-gradient(#fff,#ececec);border:1px solid #ddd}
.upload-art{left:0;top:0;width:188px;height:128px;background:linear-gradient(135deg,#5a4128,#a88a5a 50%,#3b2a1a)}
.upload-text{left:0;top:141px;width:188px;text-align:center;font-size:11px}
.upload-btn{left:22px;top:161px;width:139px;height:26px;line-height:26px}

/* content */
.heading{font-family:"Lato",sans-serif;font-size:15px;color:var(--ink);letter-spacing:.3px}
.heading em{font-style:normal;color:var(--accent-red)}
.intro{left:225px;top:437px;width:475px;font-size:10.8px;line-height:15.3px;color:var(--ink-soft)}
.intro p+p{margin-top:15px}
.more{right:35px;top:557px;font-size:9.5px;color:var(--accent-red)}
.rule{height:2px;background:linear-gradient(90deg,transparent,var(--rule) 15%,var(--rule) 85%,transparent)}

.card{top:615px;width:146px}
.card-art{width:146px;height:102px;border:1px solid #ccc;border-radius:3px}
.card-text{margin-top:8px;font-size:9.3px;line-height:11.3px;color:var(--ink-soft)}
.card-link{margin-top:4px;font-size:9.3px;color:var(--accent-red)}

.thumb{top:853px;width:149px;height:101px;border:1px solid #bbb}
.arrow{top:889px}

/* footer */
.pay-name{left:52px;top:1141px;color:#fff;font-size:16px;font-weight:700}
.cards{left:36px;top:1162px;display:flex;gap:2px}
.cards span{width:24px;height:17px;background:#d8d8d8;border:1px solid #888}
.footer-links{left:0;top:1152px;width:800px;text-align:center;color:#eee;font-size:9px;padding-right:4px}
.footer-links span{margin:0 9px}
.copyright{left:0;top:1174px;width:800px;text-align:center;color:#ddd;font-size:9px}
.social{left:590px;top:1162px;display:flex;gap:13px}
.social span{width:18px;height:18px;background:#3d5d8c;border-radius:2px}
</style>
</head>
<body>

<header>
  <div class="abs brand"><span class="brand-dot"></span><span class="brand-name">The Velvet Easel</span></div>
  <div class="abs search">
    <div class="abs search-field"></div>
    <div class="abs search-btn">Search</div>
  </div>
</header>

<main class="abs panel">
  <nav class="abs nav">
    <a style="left:35px">How It Works</a>
    <a style="left:125px">Order Your Painting</a>
    <a style="left:246px">Galleries</a>
    <a style="left:312px">Gift ideas</a>
    <a style="left:382px">Testimonials</a>
    <a style="left:468px">FAQ</a>
    <a style="left:515px">Prices</a>
    <a style="left:573px">Guarantee</a>
  </nav>

  <section class="abs hero" role="img" aria-label="Slide: abstract multi-panel painting in red, black and silver">
    <div class="abs hero-caption">Lorem ipsum dolor sit amet, consectetuer adipiscing elit Lorem ipsum dolor sit amet, adipiscing elit</div>
    <div class="abs hero-bar"></div>
    <div class="abs dots"><span></span><span></span><span></span><span></span></div>
  </section>

  <aside>
    <form class="abs login">
      <div class="abs login-head">
        <svg width="13" height="13" viewBox="0 0 13 13"><circle cx="6.5" cy="6.5" r="5.8" fill="none" stroke="#666"/><path d="M5 4l4 2.5L5 9z" fill="#666"/></svg>
        Login
      </div>
      <span class="abs field-label" style="top:49px">User Name&nbsp;:</span>
      <div class="abs field-input" style="top:46px"></div>
      <span class="abs field-label" style="top:82px">Password&nbsp;&nbsp;&nbsp;:</span>
      <div class="abs field-input" style="top:79px"></div>
      <div class="abs btn-dark submit">SUBMIT</div>
    </form>

    <div class="abs upload">
      <div class="abs upload-art" role="img" aria-label="Classical oil painting of a family gathering in a warm interior"></div>
      <p class="abs upload-text">Users will upload their photographs</p>
      <div class="abs btn-dark upload-btn">UPLOAD PHOTOGRAPHS</div>
    </div>
  </aside>

  <h1 class="abs heading" style="left:221px;top:408px">WELCOME TO <em>THE VELVET EASEL</em></h1>
  <div class="abs intro">
    <p>It is a long established fact that a reader will be distracted by the readable content of a page when looking at its layout. The point of using Lorem Ipsum is that it has a more-or-less normal distribution of letters.It is a long established fact that a reader will be distracted by the readable content of a page when looking at its layout.</p>
    <p>The point of using Lorem Ipsum is that it has a more-or-less normal distribution of letters.<br>It is a long established fact that a reader will be distracted by the readable content of a page when looking at its layout.</p>
  </div>
  <a class="abs more">View More</a>
  <div class="abs rule" style="left:215px;top:573px;width:490px"></div>

  <h2 class="abs heading" style="left:226px;top:585px">FEATURED <em>PRODUCTS</em></h2>
  <article class="abs card" style="left:227px">
    <div class="card-art" role="img" aria-label="Painting of a child with a net by a stream" style="background:linear-gradient(#4f7a3a,#a7b98a 60%,#6d8a5a)"></div>
    <p class="card-text">Uenim ad minim veniam, quis nostrud laboris nisi utaliquip ex irurdolor into</p>
    <p class="card-link">View Details</p>
  </article>
  <article class="abs card" style="left:393px">
    <div class="card-art" role="img" aria-label="Painting of a cottage beside a river in spring" style="background:linear-gradient(#c7a28a,#7f9a6a 55%,#5a7f7a)"></div>
    <p class="card-text">Uenim ad minim veniam, quis nostrud laboris nisi utaliquip ex irurdolor into</p>
    <p class="card-link">View Details</p>
  </article>
  <article class="abs card" style="left:556px">
    <div class="card-art" role="img" aria-label="Painting of two children on a bench" style="background:linear-gradient(#9bb7c9,#c8a87a 60%,#7a5a3a)"></div>
    <p class="card-text">Uenim ad minim veniam, quis nostrud laboris nisi utaliquip ex irurdolor into</p>
    <p class="card-link">View Details</p>
  </article>

  <h2 class="abs heading" style="left:37px;top:805px">LATEST <em>PRODUCTS</em></h2>
  <div class="abs rule" style="left:12px;top:827px;width:210px"></div>

  <svg class="abs arrow" style="left:12px" width="14" height="22" viewBox="0 0 14 22"><path d="M12 2L3 11l9 9" fill="none" stroke="#222" stroke-width="4"/></svg>
  <div class="abs thumb" style="left:35px;background:linear-gradient(#9bb8c0,#6f8a4a 60%,#b07a4a)" role="img" aria-label="Painting of a village garden"></div>
  <div class="abs thumb" style="left:201px;background:linear-gradient(135deg,#2f6a6a,#b8864a 50%,#8a3a2a)" role="img" aria-label="Abstract textured painting in copper and teal"></div>
  <div class="abs thumb" style="left:368px;background:linear-gradient(#9aa98a,#c9b8a0 60%,#8a9a6a)" role="img" aria-label="Still life of fruit on green cloth"></div>
  <div class="abs thumb" style="left:537px;background:linear-gradient(#cfc6b8,#9a8a7a 60%,#6a5a4a)" role="img" aria-label="Painting of a steam train at a station"></div>
  <svg class="abs arrow" style="left:693px" width="14" height="22" viewBox="0 0 14 22"><path d="M2 2l9 9-9 9" fill="none" stroke="#222" stroke-width="4"/></svg>
</main>

<footer>
  <div class="abs pay-name">Coinvale</div>
  <div class="abs cards"><span></span><span></span><span></span><span></span></div>
  <div class="abs footer-links">Privacy Policy<span>|</span>Terms &amp; Conditions<span>|</span>Contact Us</div>
  <div class="abs copyright">Copyright © 2012 Thevelveteasel,&nbsp; All rights reserved</div>
  <div class="abs social"><span></span><span></span><span></span><span></span><span></span></div>
</footer>

</body>
</html>
```